Business Card Update, need to bring life to the card, two sided color

We need a new business card design, are moving and changing addresses and need a new look, we have the logos already attached but need a new style moving forward. Can incorporate the color of the logo (The Green) as well, maybe a solid back? We deal with safety products revolving around static electricity and safety lighting. Would like to keep same font in second logo as well.

Target Market(s)

Electrical Safety, Lighting

Contact Information for Business Card

Dale Fenwick
Vice President
Office: 770-555-4821
Cell: 770-555-3067
dale@tkfenwick.example
www.tkfenwick.example
4700 West Harbor Boulevard
Suite #150
Roswell, GA 30076

Font styles to use
Serif
Sans Serif

Requirements
Must have
• Since 1918
Nice to have
• Could use the 100 Year Logo for back of card, would like the back of card to be the same green as logo.
Should not have
• No black cards please.

```html
<!DOCTYPE html>
<html lang="en">
<head>
<meta charset="utf-8">
<title>T.K. Fenwick Business Card</title>
<link href="https://fonts.googleapis.com/css2?family=Arimo:wght@700&family=Open+Sans:wght@400&display=swap" rel="stylesheet">
<style>
  :root {
    --brand-green: #00985a;
    --brand-green-soft: rgba(255, 255, 255, 0.32);
    --band-line: #bfe3d3;
    --backdrop: #e8e7ec;
    --card-white: #ffffff;
    --card-edge: #4a4a4a;
    --ink: #1c1c1c;
    --on-green: #ffffff;
    --divider: #b9b9b9;
  }
  * { margin: 0; padding: 0; box-sizing: border-box; }
  html, body { width: 1200px; height: 1049px; overflow: hidden; background: var(--backdrop); }
  .stage {
    position: absolute; left: 0; top: 0;
    width: 1179px; height: 1031px;
    transform: scale(1.0178); transform-origin: 0 0;
  }
  .card {
    position: absolute;
    border: 1px solid var(--card-edge);
    border-radius: 20px;
    overflow: hidden;
  }
  .card-front { left: 66px; top: 81px; width: 701px; height: 400px; background: var(--card-white); }
  .card-back { left: 310px; top: 518px; width: 803px; height: 458px; background: var(--brand-green); }

  .brand-mark { position: absolute; border-radius: 50%; }
  .front-mark { left: 50px; top: 131px; width: 86px; height: 86px; background: var(--brand-green); }
  .front-name {
    position: absolute; left: 146px; top: 148px;
    font-family: 'Arimo', Arial, sans-serif; font-weight: 700; color: var(--brand-green);
  }
  .front-name .name-main { display: block; font-size: 28px; line-height: 32px; }
  .front-name .name-sub { display: block; font-size: 14px; line-height: 16px; margin-left: 17px; }

  .divider {
    position: absolute; left: 420px; top: 40px; width: 2px; height: 262px;
    background: linear-gradient(to right, var(--divider), #e6e6e6);
  }
  .contact { position: absolute; left: 431px; top: 54px; right: 10px; }
  .person-name, .person-title {
    font-family: 'Arimo', Arial, sans-serif; font-weight: 700; color: var(--brand-green);
  }
  .person-name { font-size: 27px; line-height: 32px; }
  .person-title { font-size: 19px; line-height: 24px; }
  .contact-detail {
    font-family: 'Open Sans', Arial, sans-serif; font-size: 15px; color: var(--ink);
    line-height: 22px; white-space: nowrap;
  }
  .address { margin-top: 12px; }
  .detail-row { display: flex; align-items: center; gap: 6px; margin-top: 2px; }
  .address + .detail-row { margin-top: 8px; }
  .detail-row svg { width: 14px; height: 14px; flex: none; }
  .detail-label { color: var(--brand-green); }

  .email-band {
    position: absolute; left: 0; right: 0; top: 321px; height: 43px;
    border-top: 1px solid var(--band-line); border-bottom: 1px solid var(--band-line);
    padding: 2px 0;
  }
  .email-band .band-fill {
    height: 100%; background: var(--brand-green);
    display: flex; align-items: center; justify-content: center; gap: 6px;
    font-family: 'Open Sans', Arial, sans-serif; font-size: 17px; color: var(--on-green);
  }
  .email-band svg { width: 15px; height: 15px; }

  .back-mark { left: 296px; top: 22px; width: 210px; height: 210px; background: var(--brand-green-soft); }
  .back-name {
    position: absolute; left: 0; right: 0; top: 246px; text-align: center;
    font-family: 'Arimo', Arial, sans-serif; font-weight: 700; color: var(--on-green);
  }
  .back-name .name-main { display: block; font-size: 51px; line-height: 58px; }
  .back-name .name-sub { display: block; font-size: 25px; line-height: 30px; }
  .back-since {
    position: absolute; left: 0; right: 0; top: 346px; text-align: center;
    font-family: 'Arimo', Arial, sans-serif; font-weight: 700; font-size: 17px;
    letter-spacing: 3px; color: var(--on-green);
  }
  .back-web {
    position: absolute; left: 0; right: 0; top: 400px; text-align: center;
    font-family: 'Open Sans', Arial, sans-serif; font-size: 23px; letter-spacing: 4px;
    color: var(--on-green);
  }
</style>
</head>
<body>
<div class="stage">
  <section class="card card-front" aria-label="Card front">
    <div class="brand-mark front-mark"></div>
    <div class="front-name">
      <span class="name-main">T.K. Fenwick</span>
      <span class="name-sub">Manufacturing Company, Inc.</span>
    </div>
    <div class="divider"></div>
    <div class="contact">
      <p class="person-name">Dale Fenwick</p>
      <p class="person-title">Vice President</p>
      <p class="contact-detail address">4700 West Harbor Boulevard<br>Suite #150<br>Roswell, GA 30076</p>
      <p class="contact-detail detail-row">
        <svg viewBox="0 0 16 16"><circle cx="8" cy="8" r="7" fill="none" stroke="#1c1c1c" stroke-width="1.4"/><path d="M5.2 4.3l1.4-.2.8 1.8-.8.8c.5 1 1.2 1.7 2.2 2.2l.8-.8 1.8.8-.2 1.4c-3.3.3-6.3-2.7-6-6z" fill="#1c1c1c"/></svg>
        <span><span class="detail-label">Office:</span> 770-555-4821</span>
      </p>
      <p class="contact-detail detail-row">
        <svg viewBox="0 0 16 16" fill="none" stroke="#1c1c1c" stroke-width="1.3"><rect x="4.5" y="1.5" width="7" height="13" rx="1.2"/><path d="M7 12.3h2"/></svg>
        <span><span class="detail-label">Cell:</span> 770-555-3067</span>
      </p>
      <p class="contact-detail detail-row">
        <svg viewBox="0 0 16 16" fill="none" stroke="#1c1c1c" stroke-width="1.2"><circle cx="8" cy="8" r="6.5"/><ellipse cx="8" cy="8" rx="3" ry="6.5"/><path d="M1.5 8h13M2.5 5h11M2.5 11h11"/></svg>
        www.tkfenwick.example
      </p>
    </div>
    <div class="email-band">
      <div class="band-fill">
        <svg viewBox="0 0 16 16" fill="none" stroke="#fff" stroke-width="1.3"><circle cx="8" cy="8" r="7"/><rect x="4.5" y="6" width="7" height="5"/><path d="M4.5 6l3.5 3 3.5-3"/></svg>
        dale@tkfenwick.example
      </div>
    </div>
  </section>

  <section class="card card-back" aria-label="Card back">
    <div class="brand-mark back-mark"></div>
    <div class="back-name">
      <span class="name-main">T.K. Fenwick</span>
      <span class="name-sub">Manufacturing Company, Inc.</span>
    </div>
    <p class="back-since">SINCE 1918</p>
    <p class="back-web">www.tkfenwick.example</p>
  </section>
</div>
</body>
</html>
```